Veltrane Group Business Card Design

The CEO is looking for a new trendy look for his business card.
You can stay with current branding or come up with something new/creative. It can be 3D, including Medical Office buildings. You can use our logo in a variety of colors. Please include name, title, company name, company website, email address, cell number

Target Market(s)

Real Estate Development and Construction

Industry/Entity Type

Health care real estate

Contact Information for Business Card

Rohesh Kamdar, CEO M-604.781.2249 E-roheshkamdar@veltrane.com Address:4180 Lindqvist Ave, Tampa, FL 33482 www.veltrane.com

Font styles to use
Other font styles liked:
• Be creative

Requirements
Must have
• Creative, trendy look
Nice to have
• Please go to our website to get a feel- www. veltrane.com
Should not have
• small fonts

```html
<!DOCTYPE html>
<html lang="en">
<head>
<meta charset="utf-8">
<title>Veltrane Group Business Card</title>
<link rel="stylesheet" href="https://fonts.googleapis.com/css2?family=Montserrat:wght@400;500;700;800&display=swap">
<style>
  :root {
    --backdrop: #cfd4d4;
    --card-white: #f3f2ef;
    --brand-red: #b01c26;
    --deep-red: #a3111a;
    --rule-red: #e0332e;
    --ink: #3a3a3a;
    --soft-ink: #555555;
    --paper: #ffffff;
  }
  * { box-sizing: border-box; margin: 0; padding: 0; }
  html, body {
    width: 1200px;
    height: 881px;
    overflow: hidden;
    background: var(--backdrop);
    font-family: "Montserrat", Arial, sans-serif;
  }
  .canvas {
    position: relative;
    width: 1200px;
    height: 881px;
  }
  .card {
    position: absolute;
    top: 292px;
    width: 520px;
    height: 297px;
    box-shadow: 0 14px 30px rgba(0, 0, 0, 0.18);
  }
  .card-front {
    left: 60px;
    background: var(--card-white);
    border-bottom: 3px solid var(--brand-red);
  }
  .card-back {
    left: 620px;
    background: var(--deep-red);
    display: flex;
    align-items: center;
    justify-content: center;
  }
  .holder-name {
    position: absolute;
    left: 32px;
    top: 40px;
    color: var(--brand-red);
    font-weight: 700;
    font-size: 20px;
    letter-spacing: 0.5px;
    text-transform: uppercase;
  }
  .holder-title {
    position: absolute;
    left: 32px;
    top: 68px;
    color: var(--soft-ink);
    font-size: 13px;
    font-weight: 500;
  }
  .holder-address {
    position: absolute;
    left: 32px;
    top: 160px;
    color: var(--ink);
    font-size: 13px;
    font-weight: 500;
  }
  .front-brand {
    position: absolute;
    right: 32px;
    top: 88px;
    color: var(--brand-red);
    font-weight: 800;
    font-size: 30px;
    letter-spacing: -0.5px;
  }
  .front-rule {
    position: absolute;
    left: 32px;
    right: 32px;
    top: 200px;
    height: 1.5px;
    background: var(--rule-red);
  }
  .contact-row {
    position: absolute;
    left: 32px;
    right: 32px;
    top: 226px;
    display: flex;
    align-items: center;
    gap: 14px;
    color: var(--ink);
    font-size: 11.5px;
    font-weight: 500;
  }
  .contact-item {
    display: flex;
    align-items: center;
    gap: 5px;
    white-space: nowrap;
  }
  .contact-icon { width: 11px; height: 11px; flex: none; }
  .back-brand {
    color: var(--paper);
    font-weight: 800;
    font-size: 52px;
    letter-spacing: -1px;
  }
</style>
</head>
<body>
<main class="canvas">
  <section class="card card-front" aria-label="Business card front">
    <h1 class="holder-name">Rohesh Kamdar</h1>
    <p class="holder-title">CEO</p>
    <p class="front-brand">Veltrane Group</p>
    <p class="holder-address">4180 Lindqvist Ave, Tampa, FL 33482</p>
    <div class="front-rule"></div>
    <div class="contact-row">
      <span class="contact-item">
        <svg class="contact-icon" viewBox="0 0 12 12" aria-hidden="true">
          <rect x="3" y="0.5" width="6" height="11" rx="1" fill="none" stroke="#b01c26" stroke-width="1.3"/>
          <rect x="5" y="9" width="2" height="1" fill="#b01c26"/>
        </svg>604.781.2249
      </span>
      <span class="contact-item">
        <svg class="contact-icon" viewBox="0 0 12 12" aria-hidden="true">
          <rect x="0.5" y="2.5" width="11" height="7" fill="#b01c26"/>
          <polyline points="0.5,2.5 6,7 11.5,2.5" fill="none" stroke="#ffffff" stroke-width="1"/>
        </svg>roheshkamdar@veltrane.com
      </span>
      <span class="contact-item">
        <svg class="contact-icon" viewBox="0 0 12 12" aria-hidden="true">
          <circle cx="6" cy="6" r="5.5" fill="#b01c26"/>
          <ellipse cx="6" cy="6" rx="2.3" ry="5.5" fill="none" stroke="#ffffff" stroke-width="0.8"/>
          <line x1="0.5" y1="6" x2="11.5" y2="6" stroke="#ffffff" stroke-width="0.8"/>
        </svg>www.veltrane.com
      </span>
    </div>
  </section>

  <section class="card card-back" aria-label="Business card back">
    <p class="back-brand">Veltrane Group</p>
  </section>
</main>
</body>
</html>
```